MS Word Template for Proposals and RFP

Looking for a nice looking graphic template in MS Word. We will use this to make proposals and answer RFPs. Looking for something that will match our company brand, but give a fresh, up-to-date look and feel. There are a few pictures of a template I like. I don't necessarily like that logo - looks too "kid like" for business, but I really like how clean and organized it is. Most proposals and RFP responses are looooooonnnngggg and boring - need something that someone can look through and find what they are looking for quickly and easily.
Updates

Can't wait to see your designs!

Target Market(s)

School districts and other governmental employers

Industry/Entity Type

Business

Requirements
Must have
• Must include sample table of contents, section dividers, charts, graphs and tables that we customized based on the content. The goal is for it to look simple, clean, compelling - organized so it's easy to read, easy to find your way around - good headers, charts, flow charts, tables.... etc. Looking to have 5-10 template pages that we can use to put together and entire portfolio.
Should not have
• No "cutsie" comic sans/apple for the teacher kind of stuff - we are selling employee benefits to schools and other governmental entities. Should be more serious and conservative but also look compelling and draw in the reader.

```html
<!DOCTYPE html>
<html lang="en">
<head>
<meta charset="utf-8">
<title>Proposal Template – Big Text Page</title>
<link href="https://fonts.googleapis.com/css2?family=Roboto+Slab:wght@300;400&display=swap" rel="stylesheet">
<style>
  :root {
    --brand-blue: #6383c4;
    --text-blue: #5b7dc5;
    --paper: #ffffff;
    --ink-light: #ffffff;
    --footer-ink: #f2f5fb;
  }
  * { margin: 0; padding: 0; box-sizing: border-box; }
  html, body {
    width: 900px;
    height: 1200px;
    overflow: hidden;
    background: var(--paper);
  }
  .page {
    position: relative;
    width: 900px;
    height: 1200px;
    font-family: "Roboto Slab", Georgia, serif;
    font-weight: 300;
  }
  .feature-band {
    position: absolute;
    top: 0; left: 0;
    width: 900px;
    height: 715px;
    background: var(--brand-blue);
    color: var(--ink-light);
    padding: 96px 43px 0 82px;
  }
  .page-title {
    font-weight: 300;
    font-size: 40px;
    line-height: 1;
    margin-bottom: 44px;
  }
  .body-copy {
    font-size: 25.5px;
    line-height: 45px;
    text-align: justify;
    hyphens: auto;
    -webkit-hyphens: auto;
  }
  .body-copy + .body-copy { margin-top: 45px; }
  .plain-section {
    position: absolute;
    top: 772px; left: 82px;
    width: 775px;
    color: var(--text-blue);
  }
  .footer {
    position: absolute;
    left: 0; bottom: 0;
    width: 900px;
    height: 50px;
    display: flex;
  }
  .footer-edge {
    width: 12px;
    background: var(--brand-blue);
  }
  .footer-brand {
    width: 321px;
    background: var(--paper);
    display: flex;
    align-items: center;
    justify-content: center;
    gap: 10px;
    color: var(--text-blue);
    font-weight: 400;
    font-size: 20px;
    letter-spacing: 0.5px;
    text-transform: uppercase;
  }
  .brand-mark {
    width: 14px; height: 14px;
    background: var(--text-blue);
  }
  .footer-bar {
    flex: 1;
    background: var(--brand-blue);
    color: var(--footer-ink);
    font-size: 17px;
    display: flex;
    align-items: center;
    justify-content: flex-end;
    padding-right: 12px;
  }
</style>
</head>
<body>
  <div class="page">
    <section class="feature-band">
      <h1 class="page-title">Big Text</h1>
      <p class="body-copy">This template uses a few tables to create the page structure that follows. A host table consisting of just two columns and one row enables the sidebar content to sit beside the text, tables, and diagram on the left without any complicated positioning required.</p>
      <p class="body-copy">This template uses a few tables to create the page structure that follows. A host table consisting of just two columns and one row enables the sidebar content to sit beside the text, tables, and diagram on the left without any complicated positioning required.</p>
    </section>

    <section class="plain-section">
      <p class="body-copy">This template uses a few tables to create the page structure that follows. A host table consisting of just two columns and one row enables the sidebar content to sit beside the text, tables, and diagram on the left without any complicated positioning required.</p>
    </section>

    <footer class="footer">
      <div class="footer-edge"></div>
      <div class="footer-brand">
        <span class="brand-mark"></span>
        <span class="brand-name">Meridian Benefit Partners</span>
      </div>
      <div class="footer-bar">www.meridianbenefits.com</div>
    </footer>
  </div>
</body>
</html>
```